VENTURE CAPITAL GROUP BUSINESS CARD DESIGN

Venture Capital Group based in SF looking for a bold business card design. No trendy colour explosion, 3D effects etc. Just "simple" optical effects. Works on your brain, keeps your eye focused and sticks to your mind.
Target Market(s)
Technology startups
Industry/Entity Type
Venture Capital
Contact Information for Business Card
DESMOND WHITLAKE
MANAGING PARTNER
187 FENWORTH ST SAN FRANCISCO, CA 94187
415.555.0142 O
415.555.0147 F
415.555.0193 C
desmond@veldtmoorcapital.ventures

```html
<!DOCTYPE html>
<html lang="en">
<head>
<meta charset="utf-8">
<title>Veldtmoor Capital Group – Business Card</title>
<link rel="stylesheet" href="https://fonts.googleapis.com/css2?family=Merriweather:wght@300;400&family=Saira+Semi+Condensed:wght@600&display=swap">
<style>
  :root {
    --backdrop: #aeabab;
    --card: #16181b;
    --brand-green: #2e9a44;
    --accent-green: #6cc12a;
    --text-light: #d9d9d9;
    --text-muted: #bdbdbd;
    --disc: #202226;
    --disc-edge: #3a3c40;
  }
  * { margin: 0; padding: 0; box-sizing: border-box; }
  html, body { width: 1200px; height: 1200px; overflow: hidden; }
  body {
    background: var(--backdrop);
    position: relative;
    font-family: "Merriweather", Georgia, serif;
  }
  .card {
    position: absolute;
    left: 242px;
    width: 716px;
    height: 420px;
    background: var(--card);
  }
  .card--front { top: 110px; }
  .card--back { top: 640px; }

  .brand-disc {
    position: absolute;
    border-radius: 50%;
    background: var(--disc);
    border: 1px solid var(--disc-edge);
  }
  .card--front .brand-disc { left: 272px; top: 84px; width: 168px; height: 168px; }
  .card--back .brand-disc { left: 51px; top: 96px; width: 222px; height: 222px; }

  .brand-name {
    position: absolute;
    left: 0; right: 0;
    text-align: center;
    color: var(--brand-green);
    font-weight: 400;
  }
  .brand-name__main { top: 268px; font-size: 40px; letter-spacing: 1px; }
  .brand-name__sub { top: 322px; font-size: 13px; letter-spacing: 6px; }

  .card--back .brand-name {
    left: 51px; right: auto; width: 222px;
    top: 330px;
    font-size: 12px;
    letter-spacing: 2px;
  }

  .contact-block { position: absolute; left: 331px; top: 92px; }
  .person-name {
    font-family: "Saira Semi Condensed", "Arial Narrow", sans-serif;
    font-weight: 600;
    font-size: 28px;
    color: var(--accent-green);
    line-height: 1.1;
  }
  .person-title {
    font-size: 15px;
    font-weight: 300;
    color: var(--text-muted);
    margin-top: 4px;
  }
  .contact-list { list-style: none; margin-top: 42px; }
  .contact-list li {
    display: flex;
    align-items: center;
    height: 22px;
    font-size: 16px;
    font-weight: 300;
    color: var(--text-light);
  }
  .contact-list svg { width: 18px; height: 16px; margin-right: 16px; fill: var(--accent-green); flex: none; }
  .web-highlight { color: var(--accent-green); }
  .address {
    margin-top: 6px;
    font-size: 16px;
    font-weight: 300;
    color: var(--text-light);
  }
</style>
</head>
<body>
  <section class="card card--front">
    <div class="brand-disc"></div>
    <div class="brand-name brand-name__main">VELDTMOOR</div>
    <div class="brand-name brand-name__sub">CAPITAL GROUP</div>
  </section>

  <section class="card card--back">
    <div class="brand-disc"></div>
    <div class="brand-name">VELDTMOOR CAPITAL GROUP</div>

    <div class="contact-block">
      <h1 class="person-name">Desmond Whitlake</h1>
      <p class="person-title">Managing Partner</p>
      <ul class="contact-list">
        <li><svg viewBox="0 0 18 16"><path d="M1 5c0-2 3-4 8-4s8 2 8 4v2h-4V5H5v2H1zM4 8h10l2 7H2z"/></svg>415.555.0142</li>
        <li><svg viewBox="0 0 18 16"><path d="M4 1h10v4H4zM1 6h16v7h-3v-3H4v3H1zM5 11h8v4H5z"/></svg>415.555.0147</li>
        <li><svg viewBox="0 0 18 16"><path d="M6 0h7v16H6zM7.5 2v10h4V2z"/></svg>415.555.0193</li>
        <li><svg viewBox="0 0 18 16"><path d="M1 3h16v10H1zM2.5 4.5 9 9l6.5-4.5v1L9 10 2.5 5.5z" fill-rule="evenodd"/></svg>desmond@veldtmoorcapital.ventures</li>
        <li><svg viewBox="0 0 18 16"><circle cx="9" cy="8" r="7"/><path d="M2 8h14M9 1v14M4 4h10M4 12h10" stroke="#16181b" stroke-width="1"/></svg>www.<span class="web-highlight">veldtmoorcapital</span>.ventures</li>
      </ul>
      <p class="address">187 Fenworth St San Francisco, CA 94187</p>
    </div>
  </section>
</body>
</html>
```